Mortgage Company ready to make a statement!

We have a basic logo that I am fairly happy with ... but it could use a little bit of tweaking before we order the sign for our building. We also want some knock-your-socks-off business cards.
Problem: Inside of our Mortgage Office (Bright Fern Mortgage Group), we are going to have a coffee lounge (Sunbrew Cafe) for Realtors to use instead of the local Cuppington to meet with homebuyers. The office and coffee lounge are in an industrial building and is decorated with cozy overstuffed chairs, a hodge podge of interesting lamps and furniture, and goal is to make it as inviting as possible. However, we are a financial institution... so we need to keep it pretty clean as well.
One of my favorite marketing ideas is to cut a house key for everyone who buys a home using us with a key that matches our logo. There's only one key shape that works really well, so that needs to match the logo in order for the idea to work. I'll attach an image of the key blank.... although the way the key hole cut out looks terrible, so I was thinking of having them just do a thin outline instead.
Would like a similar, matching logo for the Sunbrew Cafe... but possibly something that would be a little less formal and would be cute on a coffee mug- nothing stuffy.
AND, we're opening a home inspection company as well, and we would like that logo and branding to match. The home inspection company is "Bright Fern Home Inspections"
We were thinking that for the home inspection company , we could use a magnifying glass shape inside of the house shape for the logo, use a keyhole shape inside of the same house for the mortgage company, and use a coffee cup inside of the house shape for Sunbrew Cafe.
Just getting stuck and need to help. I designed the attached logo myself, and that is what we are currently using. Designers at local printing companies have failed to impress us.
The mortgage industry has a lot of numbers and logos, etc that they require us to put on our business cards... so it's hard to keep them looking clean.
HELP! HELP! :)

```html
<!DOCTYPE html>
<html lang="en">
<head>
<meta charset="utf-8">
<title>Bright Fern Mortgage Group – Business Card</title>
<link href="https://fonts.googleapis.com/css2?family=Lato:wght@400;700&family=Cinzel:wght@700&display=swap" rel="stylesheet">
<style>
  :root {
    --brand-blue: #216585;
    --brand-slate: #4f4c5c;
    --card-white: #ffffff;
    --ink: #2a2a2a;
    --backdrop: #ecebe8;
  }
  * { box-sizing: border-box; margin: 0; padding: 0; }
  html, body {
    width: 1200px; height: 900px; overflow: hidden;
    background: var(--backdrop);
    font-family: "Lato", Arial, sans-serif;
  }
  .stage {
    position: relative; width: 1200px; height: 900px;
  }
  .card {
    position: absolute; left: 250px;
    width: 700px; height: 400px;
    box-shadow: 0 6px 18px rgba(0,0,0,0.15);
    overflow: hidden;
  }
  .card--front { top: 40px; background: var(--brand-blue); display: flex; align-items: center; justify-content: center; }
  .card--back { top: 470px; background: var(--card-white); }

  .wordmark {
    display: flex; align-items: center; gap: 18px;
    font-family: "Lato", Arial, sans-serif; font-weight: 400;
    letter-spacing: 1px;
  }
  .wordmark__mark { width: 18px; height: 18px; border-radius: 50%; }
  .card--front .wordmark { color: var(--card-white); font-size: 40px; }
  .card--front .wordmark__mark { background: var(--card-white); }

  .card--back .wordmark {
    position: absolute; top: 62px; right: 40px;
    color: var(--brand-blue); font-size: 24px;
  }
  .card--back .wordmark__mark { width: 14px; height: 14px; background: var(--brand-blue); }

  .holder { position: absolute; top: 70px; left: 44px; }
  .holder__name {
    font-family: "Cinzel", Georgia, serif; font-weight: 700;
    color: var(--brand-blue); font-size: 22px; letter-spacing: 0.5px;
  }
  .holder__role { font-size: 15px; font-weight: 700; color: var(--ink); margin-top: 2px; margin-left: 6px; }

  .contact { position: absolute; top: 175px; left: 50px; color: var(--ink); font-size: 17px; line-height: 1.3; }
  .contact__address { margin-bottom: 12px; }
  .contact__line { display: flex; align-items: center; gap: 10px; }
  .contact__icon { width: 14px; height: 14px; fill: var(--brand-blue); }

  .wave { position: absolute; inset: 0; width: 700px; height: 400px; }
  .website {
    position: absolute; right: 26px; top: 300px;
    color: var(--card-white); font-size: 13px; letter-spacing: 0.3px;
  }
</style>
</head>
<body>
<main class="stage">
  <section class="card card--front" aria-label="Card front">
    <div class="wordmark"><span class="wordmark__mark"></span><span>Bright Fern Mortgage Group</span></div>
  </section>

  <section class="card card--back" aria-label="Card back">
    <svg class="wave" viewBox="0 0 700 400" aria-hidden="true">
      <path d="M0,335 C170,385 390,335 575,228 C420,345 200,390 0,360 Z" fill="var(--brand-slate)"/>
      <path d="M0,376 C190,405 430,335 700,170 L700,400 L0,400 Z" fill="var(--brand-blue)"/>
    </svg>

    <div class="holder">
      <h1 class="holder__name">DANIEL MARSH</h1>
      <p class="holder__role">Managing Director</p>
    </div>

    <div class="wordmark"><span class="wordmark__mark"></span><span>Bright Fern Mortgage Group</span></div>

    <div class="contact">
      <p class="contact__address">1234, Address GoesHere,<br>Country name, 12345</p>
      <p class="contact__line">
        <svg class="contact__icon" viewBox="0 0 24 24"><path d="M6.6 10.8a15 15 0 0 0 6.6 6.6l2.2-2.2a1 1 0 0 1 1-.25 11.4 11.4 0 0 0 3.6.57 1 1 0 0 1 1 1V20a1 1 0 0 1-1 1A17 17 0 0 1 3 4a1 1 0 0 1 1-1h3.5a1 1 0 0 1 1 1c0 1.25.2 2.450.57 3.57a1 1 0 0 1-.25 1z"/></svg>
        (044)555014200
      </p>
      <p class="contact__line">
        <svg class="contact__icon" viewBox="0 0 24 24"><path d="M2 5h20v14H2z M2 5l10 8 10-8" fill="var(--brand-blue)" stroke="#fff" stroke-width="1.5"/></svg>
        hello@brightfern.com
      </p>
    </div>

    <p class="website">www.brightfernmortgage.com</p>
  </section>
</main>
</body>
</html>
```